RW Holloway LLC Business Card - Civil Engineering & Consulting Firm

We need a Business Card that is elegant, and masculine.  It is our Professional Civil Engineering & Consulting Company located in San Antonio TX (Not s construction or builder firm- no gears & no tool images please). We provide civil engineering services including  commercial site plans, grading and drainage plans, utility plans, hydraulics and hydrology, land planning, utility coordination, and other general civil engineering services related to commercial and residential development.
We have 2 existing Logos. We would like to convey reliability, strength, trustworthiness and attention to detail.  Blues and orange tones as per logo We are OK with the use of a darker blue in the mix.  We have 2 logo versions - Full Company Name Logo to go on the back of card, & Small Icon Logo for the front w/ personal Info.

Target Market(s)
Architects, Real Estate Developers, Other Strctural Engineers, Surveyers, General Contractors
Industry/Entity Type
Professional Civil Engineering
Contact Information for Business Card
Name, Position, Address, Cell & Office #, email, and company website
Font styles to use
Other font styles liked:
- Avian
Requirements
Should not have
- No Tools, No Gears, no Cranes, or Construction Equipment.

```html
<!DOCTYPE html>
<html lang="en">
<head>
<meta charset="utf-8">
<title>RW Holloway LLC – Business Card</title>
<link href="https://fonts.googleapis.com/css2?family=Josefin+Sans:wght@300;400&family=Arimo:wght@400&display=swap" rel="stylesheet">
<style>
  :root {
    --stage: #2b2b2d;
    --card: #161616;
    --blue: #6fa6d6;
    --orange: #f39a2b;
    --white: #f4f4f4;
    --shadow: rgba(0,0,0,0.55);
  }
  * { margin: 0; padding: 0; box-sizing: border-box; }
  html, body {
    width: 1200px; height: 1015px; overflow: hidden;
    background: var(--stage);
  }
  .stage {
    width: 1200px; height: 1015px;
    display: flex; flex-direction: column; align-items: center;
    justify-content: center; gap: 32px;
  }
  .card {
    position: relative;
    width: 760px; height: 434px;
    background: var(--card);
    box-shadow: 0 10px 28px var(--shadow);
    overflow: hidden;
  }
  .brand {
    font-family: "Josefin Sans", sans-serif;
    font-weight: 300;
    color: var(--blue);
    letter-spacing: 0.06em;
    line-height: 1;
  }
  .brand-rule { height: 2px; background: var(--blue); }
  .tagline {
    font-family: "Josefin Sans", sans-serif;
    font-weight: 300;
    color: var(--orange);
    letter-spacing: 0.42em;
    text-transform: uppercase;
  }

  /* Logo side */
  .card--logo .lockup {
    position: absolute; left: 50%; top: 50%;
    transform: translate(-50%, -50%);
    display: flex; flex-direction: column; align-items: flex-start;
  }
  .card--logo .brand { font-size: 76px; }
  .card--logo .brand-rule { width: 100%; margin: 14px 0 14px; }
  .card--logo .tagline { font-size: 17px; }

  /* Contact side */
  .card--contact .lockup {
    position: absolute; left: 80px; top: 62px;
    display: flex; flex-direction: column; align-items: flex-start;
  }
  .card--contact .brand { font-size: 60px; }
  .card--contact .brand-rule { width: 100%; margin: 12px 0 12px; }
  .card--contact .tagline { font-size: 14px; }

  .accent-square {
    position: absolute; left: 42px; top: 262px;
    width: 52px; height: 52px; background: var(--blue);
  }
  .person {
    position: absolute; left: 118px; top: 252px;
    font-family: "Arimo", sans-serif;
  }
  .person-name {
    font-size: 26px; letter-spacing: 0.02em; text-transform: uppercase;
    color: var(--blue); line-height: 1.1;
  }
  .person-name .surname { color: var(--orange); }
  .person-role { font-size: 19px; color: var(--white); margin-top: 2px; }
  .contact-list {
    list-style: none; margin-top: 18px;
    font-size: 19px; color: var(--white);
  }
  .contact-list li {
    display: flex; align-items: center; gap: 10px; height: 28px;
  }
  .contact-list svg { width: 18px; height: 18px; flex: none; }
  .contact-list .hl { color: var(--orange); }
</style>
</head>
<body>
<main class="stage">

  <section class="card card--logo" aria-label="Business card, logo side">
    <div class="lockup">
      <div class="brand">HOLLOWAY LLC</div>
      <div class="brand-rule"></div>
      <div class="tagline">Consulting Engineers</div>
    </div>
  </section>

  <section class="card card--contact" aria-label="Business card, contact side">
    <div class="lockup">
      <div class="brand">HOLLOWAY LLC</div>
      <div class="brand-rule"></div>
      <div class="tagline">Consulting Engineers</div>
    </div>

    <div class="accent-square"></div>

    <div class="person">
      <div class="person-name">Marcus <span class="surname">Reed</span></div>
      <div class="person-role">Managing Director</div>
      <ul class="contact-list">
        <li>
          <svg viewBox="0 0 20 20" aria-hidden="true"><path d="M5 2l3 4-2 2c1 2 3 4 5 5l2-2 4 3-2 3c-6 0-13-7-13-13z" fill="var(--blue)"/></svg>
          044-555 210 734
        </li>
        <li>
          <svg viewBox="0 0 20 20" aria-hidden="true"><rect x="1" y="4" width="18" height="12" fill="var(--blue)"/><path d="M1 4l9 7 9-7" stroke="var(--card)" stroke-width="1.6" fill="none"/></svg>
          info@hollowayce.com
        </li>
        <li>
          <svg viewBox="0 0 20 20" aria-hidden="true"><circle cx="10" cy="10" r="8" fill="none" stroke="var(--blue)" stroke-width="1.8"/><path d="M2 10h16M10 2v16M4 6h12M4 14h12" stroke="var(--blue)" stroke-width="1.2"/></svg>
          <span>www.<span class="hl">hollowayce</span>.com</span>
        </li>
      </ul>
    </div>
  </section>

</main>
</body>
</html>
```